Frostvale Harborline LLC

we need a business card design

Industry/Entity Type

hvac

Contact Information for Business Card

my logo

Requirements
Must have
• my logo and same colors

```html
<!DOCTYPE html>
<html lang="en">
<head>
<meta charset="utf-8">
<title>Frostvale Harborline LLC — Business Card</title>
<link href="https://fonts.googleapis.com/css2?family=Montserrat:wght@500;700&display=swap" rel="stylesheet">
<style>
  :root {
    --brand-blue: #1c5fae;
    --brand-blue-deep: #184f94;
    --brand-gold: #f4b43a;
    --ink: #1f2a3a;
    --paper: #ffffff;
    --stage: #e9ecf0;
  }
  * { margin: 0; padding: 0; box-sizing: border-box; }
  html, body { width: 1200px; height: 874px; overflow: hidden; }
  body {
    background: var(--stage);
    font-family: "Montserrat", Arial, sans-serif;
    position: relative;
  }
  .card {
    position: absolute;
    left: 280px;
    width: 640px;
    height: 366px;
    border-radius: 22px;
    overflow: hidden;
    box-shadow: 0 6px 20px rgba(0,0,0,0.18);
  }
  .card-front { top: 46px; background: var(--brand-blue); }
  .card-back { top: 462px; background: var(--paper); }

  .front-name {
    position: absolute;
    inset: 0;
    display: flex;
    align-items: center;
    justify-content: center;
    gap: 16px;
  }
  .front-name .mark-dot {
    width: 30px; height: 30px; border-radius: 50%;
    background: var(--brand-gold);
  }
  .front-name span {
    font-weight: 700;
    font-size: 34px;
    color: var(--paper);
    letter-spacing: 0.5px;
  }

  .back-wave { position: absolute; inset: 0; }
  .back-name {
    position: absolute;
    left: 34px; top: 118px;
    width: 230px;
    display: flex; align-items: center; gap: 10px;
  }
  .back-name .mark-dot {
    flex: none; width: 20px; height: 20px; border-radius: 50%;
    background: var(--brand-gold);
  }
  .back-name span {
    font-weight: 700; font-size: 21px; line-height: 1.2;
    color: var(--brand-blue);
  }
  .divider {
    position: absolute; left: 292px; top: 96px;
    width: 3px; height: 160px; background: var(--brand-blue);
  }
  .contact { position: absolute; left: 310px; top: 96px; color: var(--ink); }
  .contact .person {
    font-weight: 700; font-size: 25px; color: var(--brand-blue); line-height: 1.1;
  }
  .contact .role { font-weight: 500; font-size: 14px; margin-bottom: 10px; }
  .contact .address { font-weight: 500; font-size: 14px; line-height: 1.3; margin-bottom: 6px; }
  .contact .line {
    display: flex; align-items: center; gap: 9px;
    font-weight: 500; font-size: 14px; line-height: 1.55;
  }
  .contact .line svg { width: 13px; height: 13px; flex: none; }
</style>
</head>
<body>
  <section class="card card-front" aria-label="Card front">
    <div class="front-name">
      <div class="mark-dot"></div>
      <span>Frostvale Harborline LLC</span>
    </div>
  </section>

  <section class="card card-back" aria-label="Card back">
    <svg class="back-wave" viewBox="0 0 640 366" preserveAspectRatio="none">
      <path d="M0 200 C 140 330, 420 350, 640 330 L640 366 L0 366 Z" fill="var(--brand-blue)"/>
      <path d="M60 222 C 200 320, 430 340, 600 330" fill="none" stroke="var(--brand-gold)" stroke-width="5" stroke-linecap="round"/>
    </svg>
    <div class="back-name">
      <div class="mark-dot"></div>
      <span>Frostvale Harborline LLC</span>
    </div>
    <div class="divider"></div>
    <div class="contact">
      <div class="person">Dana Mercer</div>
      <div class="role">Managing Director</div>
      <div class="address">48 Quayside Lane,<br>Harbor City, FL 33601</div>
      <div class="line">
        <svg viewBox="0 0 12 12"><rect x="3" y="0.5" width="6" height="11" rx="1.2" fill="none" stroke="var(--brand-gold)" stroke-width="1.3"/></svg>
        +1 (555) 014-2290
      </div>
      <div class="line">
        <svg viewBox="0 0 12 12"><rect x="0.5" y="2" width="11" height="8" fill="var(--brand-gold)"/><path d="M0.5 2 L6 6.5 L11.5 2" fill="none" stroke="#fff" stroke-width="1"/></svg>
        hello@frostvaleharbor.com
      </div>
      <div class="line">
        <svg viewBox="0 0 12 12"><circle cx="6" cy="6" r="5.3" fill="none" stroke="var(--brand-gold)" stroke-width="1.3"/><path d="M0.8 6 H11.2 M6 0.8 C3.5 4 3.5 8 6 11.2 M6 0.8 C8.5 4 8.5 8 6 11.2" fill="none" stroke="var(--brand-gold)" stroke-width="1"/></svg>
        www.frostvaleharbor.com
      </div>
    </div>
  </section>
</body>
</html>
```